Weightloss company needs Business Card

We want a business card that is clean and professional, yet portrays that we are a friendly, innovative, and versatile program designed to fit the needs of our clients.
I would like there to be 2 sides, one side having an appointment card, and the other side containing the logo and business information. There can be decorations on both sides. The logo is attached.

Target Market(s)

Men and women 40-60

Industry/Entity Type

Business

Contact Information for Business Card

Font styles to use
Sans Serif

Requirements
Must have
• The logo, space for business information
Nice to have
• The colors in the logo
Should not have
• No pictures of people or food

```html
<!DOCTYPE html>
<html lang="en">
<head>
<meta charset="utf-8">
<title>Brightstep Weightloss – Business Card</title>
<link rel="stylesheet" href="https://fonts.googleapis.com/css2?family=Open+Sans:wght@400;600;700&display=swap">
<style>
  :root {
    --brand-red: #e8103f;
    --brand-red-dark: #c70a33;
    --brand-cyan: #2bbfd9;
    --ink: #3a3a3a;
    --rule: #555;
    --paper: #ffffff;
    --paper-shade: #e9e9e9;
    --backdrop: #d9d6d0;
  }
  * { box-sizing: border-box; margin: 0; padding: 0; }
  html, body { width: 1200px; height: 843px; overflow: hidden; }
  body {
    background: var(--backdrop);
    font-family: "Open Sans", sans-serif;
    position: relative;
  }
  .card {
    position: absolute;
    top: 267px;
    width: 540px;
    height: 309px;
    border-radius: 16px;
    overflow: hidden;
    box-shadow: 0 10px 24px rgba(0,0,0,.25);
  }

  /* Appointment side */
  .card--appointment {
    left: 40px;
    background: linear-gradient(160deg, var(--paper) 45%, var(--paper-shade));
    color: var(--ink);
  }
  .appointment__title {
    position: absolute; left: 30px; top: 62px;
    font-size: 19px; font-weight: 700; color: var(--brand-red);
  }
  .appointment__rows {
    position: absolute; left: 30px; top: 102px; right: 26px;
    list-style: none;
  }
  .appointment__row {
    display: flex; align-items: flex-end; gap: 8px;
    height: 46px; font-size: 13px;
  }
  .appointment__line { border-bottom: 1px solid var(--rule); height: 1px; margin-bottom: 4px; }
  .appointment__line--date { width: 168px; }
  .appointment__line--time { width: 110px; }
  .appointment__label--time { margin-left: 14px; }
  .appointment__note {
    position: absolute; left: 30px; bottom: 22px;
    font-size: 10.5px; font-weight: 600; color: #555;
  }

  /* Brand lockup */
  .brand {
    position: absolute;
    display: flex; align-items: center; gap: 8px;
    color: var(--brand-red); font-weight: 700; line-height: 1;
  }
  .brand__dot {
    border-radius: 50%;
    border: 3px solid var(--brand-red);
  }
  .card--appointment .brand { right: 24px; top: 20px; font-size: 17px; }
  .card--appointment .brand__dot { width: 26px; height: 26px; }

  /* Contact side */
  .card--contact { left: 620px; background: var(--paper); }
  .contact__art { position: absolute; inset: 0; }
  .contact__name {
    position: absolute; left: 28px; top: 22px;
    font-size: 17px; font-weight: 600; color: var(--brand-red); letter-spacing: .5px;
  }
  .contact__role {
    position: absolute; left: 28px; top: 44px;
    font-size: 12px; color: var(--brand-cyan);
  }
  .card--contact .brand { left: 40px; top: 86px; font-size: 28px; }
  .card--contact .brand__dot { width: 44px; height: 44px; border-width: 4px; }
  .contact__address {
    position: absolute; left: 26px; top: 196px;
    font-style: normal; font-size: 13.5px; line-height: 1.35; color: var(--paper);
  }
  .contact__list {
    position: absolute; right: 20px; top: 222px;
    list-style: none; color: var(--paper); font-size: 13px; line-height: 1;
  }
  .contact__item {
    display: flex; justify-content: flex-end; align-items: center; gap: 8px;
    height: 19px;
  }
  .contact__icon { width: 13px; height: 13px; fill: none; stroke: var(--paper); stroke-width: 1.6; }
</style>
</head>
<body>

<section class="card card--appointment" aria-label="Appointment card">
  <div class="brand"><span class="brand__dot"></span><span class="brand__name">Brightstep Weightloss</span></div>
  <h2 class="appointment__title">Next Appointment</h2>
  <ul class="appointment__rows">
    <li class="appointment__row"><span>Date</span><span class="appointment__line appointment__line--date"></span><span class="appointment__label--time">Time</span><span class="appointment__line appointment__line--time"></span><span>am/pm</span></li>
    <li class="appointment__row"><span>Date</span><span class="appointment__line appointment__line--date"></span><span class="appointment__label--time">Time</span><span class="appointment__line appointment__line--time"></span><span>am/pm</span></li>
    <li class="appointment__row"><span>Date</span><span class="appointment__line appointment__line--date"></span><span class="appointment__label--time">Time</span><span class="appointment__line appointment__line--time"></span><span>am/pm</span></li>
  </ul>
  <p class="appointment__note">Please give 24 hours notice of cancellation or a fee may be charged</p>
</section>

<section class="card card--contact" aria-label="Contact card">
  <svg class="contact__art" viewBox="0 0 540 309" width="540" height="309" aria-hidden="true">
    <defs>
      <linearGradient id="redBand" x1="0" y1="0" x2="1" y2="1">
        <stop offset="0" stop-color="#f0204c"/>
        <stop offset="1" stop-color="#c70a33"/>
      </linearGradient>
    </defs>
    <path d="M0,130 C90,200 260,248 540,168 L540,186 C300,258 110,230 0,150 Z" fill="var(--brand-cyan)"/>
    <path d="M0,142 C100,215 290,262 540,184 L540,309 L0,309 Z" fill="url(#redBand)"/>
  </svg>

  <h1 class="contact__name">DANA WHITFIELD</h1>
  <p class="contact__role">CEO/FOUNDER</p>
  <div class="brand"><span class="brand__name">Brightstep Weightloss</span><span class="brand__dot"></span></div>

  <address class="contact__address">1420 Alder Court<br>Juneau, Alaska 99801</address>

  <ul class="contact__list">
    <li class="contact__item">907 555 0142
      <svg class="contact__icon" viewBox="0 0 16 16"><path d="M3 1.5l3 .5 1 3.5-2 1.2a9 9 0 0 0 4.8 4.8l1.2-2 3.5 1 .5 3c-7 1-13-5-12-12z"/></svg></li>
    <li class="contact__item">907 555 0187
      <svg class="contact__icon" viewBox="0 0 16 16"><rect x="4" y="1" width="8" height="14" rx="1.5"/><path d="M7 12.5h2"/></svg></li>
    <li class="contact__item">dana@brightstep.com
      <svg class="contact__icon" viewBox="0 0 16 16"><rect x="1.5" y="3.5" width="13" height="9" rx="1"/><path d="M1.5 4l6.5 5 6.5-5"/></svg></li>
    <li class="contact__item">www.brightstep.com
      <svg class="contact__icon" viewBox="0 0 16 16"><circle cx="8" cy="8" r="6.5"/><path d="M1.5 8h13M8 1.5c-3 3.5-3 9.5 0 13M8 1.5c3 3.5 3 9.5 0 13"/></svg></li>
  </ul>
</section>

</body>
</html>
```